Law Offices business card

Hi there, I'll need business card for the Law Offices of Colin Matheny. The information must convey his strategic approach and quick resolution to complex business litigation needs. Please emphasize Civil Litigation, Corporate Law, Business Governance and Real Estate Law. Colin has over 25 years of experience in these fields.The card should be modern and edgy and the message should be clear. Please consult his current website for ideas.

```html
<!DOCTYPE html>
<html lang="en">
<head>
<meta charset="utf-8">
<title>Law Offices of Colin Matheny – Business Card</title>
<link rel="stylesheet" href="https://fonts.googleapis.com/css2?family=Lato:wght@400;700&family=Roboto+Condensed:wght@600;700&display=swap">
<style>
  :root {
    --stage: #000000;
    --paper: #f2f2f2;
    --brand-orange: #fb5d05;
    --ink: #2b2b2b;
    --rule-grey: #555555;
    --white: #ffffff;
  }
  * { margin: 0; padding: 0; box-sizing: border-box; }
  html, body { width: 1200px; height: 900px; overflow: hidden; background: var(--stage); }
  .canvas { position: relative; width: 1200px; height: 900px; }

  .card { position: absolute; top: 200px; width: 310px; height: 502px; }
  .card--front { left: 265px; background: var(--paper); border-radius: 52px 0 52px 0; }
  .card--back { left: 641px; background: var(--brand-orange); border-radius: 0 52px 0 52px; }

  .brand { position: absolute; left: 0; right: 0; text-align: center; }
  .card--front .brand { top: 56px; }
  .card--back .brand { top: 61px; }
  .brand__mark { display: block; width: 26px; height: 26px; margin: 0 auto 58px; }
  .card--front .brand__mark { background: var(--brand-orange); }
  .card--back .brand__mark { background: var(--white); }
  .brand__name {
    font-family: "Roboto Condensed", "Arial Narrow", sans-serif;
    font-weight: 600; font-size: 28px; line-height: 30px; letter-spacing: -0.2px;
  }
  .brand__surname {
    display: flex; align-items: center; gap: 8px; width: 236px; margin: 0 auto;
    font-family: "Roboto Condensed", "Arial Narrow", sans-serif;
    font-weight: 700; font-size: 19px; line-height: 24px; letter-spacing: 0.6px;
  }
  .brand__surname::before, .brand__surname::after { content: ""; flex: 1; height: 1px; }
  .card--front .brand__name { color: var(--brand-orange); }
  .card--front .brand__surname { color: var(--ink); }
  .card--front .brand__surname::before, .card--front .brand__surname::after { background: var(--rule-grey); }
  .card--back .brand__name, .card--back .brand__surname { color: var(--white); }
  .card--back .brand__surname::before, .card--back .brand__surname::after { background: var(--white); }

  .contact { position: absolute; left: 26px; top: 299px; font-family: "Lato", Arial, sans-serif; color: var(--ink); }
  .contact__name { color: var(--brand-orange); font-weight: 700; font-size: 18px; line-height: 22px; }
  .contact__role { font-size: 13.5px; line-height: 18px; }
  .contact__address { margin-top: 9px; font-size: 13.5px; line-height: 19px; font-style: normal; }
  .contact__list { list-style: none; margin-top: 10px; }
  .contact__item { display: flex; align-items: center; font-size: 13.5px; line-height: 20.6px; }
  .contact__icon { width: 11px; height: 11px; margin: 0 6px 0 1px; fill: var(--brand-orange); flex: none; }

  .services { position: absolute; left: 22px; top: 330px; list-style: none;
    font-family: "Lato", Arial, sans-serif; font-weight: 700; font-size: 15px; line-height: 23px; color: var(--white); }
  .services li { position: relative; padding-left: 14px; }
  .services li::before { content: ""; position: absolute; left: 0; top: 9px; width: 6px; height: 6px; border-radius: 50%; background: var(--white); }
  .experience { position: absolute; left: 22px; top: 432px;
    font-family: "Lato", Arial, sans-serif; font-weight: 400; font-size: 13.5px; line-height: 19px; color: var(--white); }
</style>
</head>
<body>
<main class="canvas">
  <section class="card card--front" aria-label="Card front">
    <div class="brand">
      <span class="brand__mark"></span>
      <p class="brand__name">Law Offices of Colin</p>
      <p class="brand__surname">Matheny</p>
    </div>
    <div class="contact">
      <p class="contact__name">Colin Matheny</p>
      <p class="contact__role">Attorney</p>
      <address class="contact__address">512B Harbor Lane<br>Palm Grove, Florida 33410</address>
      <ul class="contact__list">
        <li class="contact__item">
          <svg class="contact__icon" viewBox="0 0 12 12" aria-hidden="true"><path d="M2.5 0.8 4.3 3 3.4 4.3c.7 1.6 2.1 3 3.7 3.7L8.4 7l2.2 1.8-.9 2.2C5.4 11.2.8 6.6 1 2.3z"/></svg>555-214-3078</li>
        <li class="contact__item">
          <svg class="contact__icon" viewBox="0 0 12 12" aria-hidden="true"><path d="M3 0h5v3H3zM1 4h10v7H1zm2 2v1h2V6zm4 0v1h2V6zM3 8v1h2V8zm4 0v1h2V8z"/></svg>555-386-4105</li>
        <li class="contact__item">
          <svg class="contact__icon" viewBox="0 0 12 12" aria-hidden="true"><path d="M0 2h12v1L6 7 0 3zm0 2.2 6 4 6-4V10H0z"/></svg>colin@mathenylaw.com</li>
        <li class="contact__item">
          <svg class="contact__icon" viewBox="0 0 12 12" aria-hidden="true"><circle cx="6" cy="6" r="5.5"/><path d="M3 4c1 0 2 1 2 2s-1 1-1 3M8 2c0 1 1 1 2 2" stroke="#f2f2f2" stroke-width="1" fill="none"/></svg>www.mathenylaw.com</li>
      </ul>
    </div>
  </section>

  <section class="card card--back" aria-label="Card back">
    <div class="brand">
      <span class="brand__mark"></span>
      <p class="brand__name">Law Offices of Colin</p>
      <p class="brand__surname">Matheny</p>
    </div>
    <ul class="services">
      <li>Civil Litigation</li>
      <li>Corporate Law</li>
      <li>Business Governance</li>
      <li>Real Estate Law</li>
    </ul>
    <p class="experience">Over 25 years of experience</p>
  </section>
</main>
</body>
</html>
```